Management consulting Company in the electronic payment ecosystem needs a Website

We need to have a "showcase" style website that contains the key message that our company is able to provide management consulting in the world of payment systems. Our mission is to assist our clients in reviewing their sales, purchasing, operation and IT processes and to support them in identifying the best solution in the use of payment systems.

```html
<!DOCTYPE html>
<html lang="en">
<head>
<meta charset="utf-8">
<title>Tallo Consulting</title>
<link rel="stylesheet" href="https://fonts.googleapis.com/css2?family=Montserrat:wght@300;400;500;600;700;900&display=swap">
<style>
:root{
  --navy:#0d1b5e;
  --navy-deep:#0b1850;
  --ink:#141414;
  --text:#6d6d6d;
  --band:#f1f1f1;
  --white:#ffffff;
}
*{box-sizing:border-box;margin:0;padding:0}
html,body{width:1200px;height:2735px;overflow:hidden}
body{font-family:'Montserrat',sans-serif;color:var(--ink);background:var(--white);position:relative}
.abs{position:absolute}

/* header */
.site-header{position:absolute;top:0;left:0;width:1200px;height:75px;background:var(--white)}
.brand{position:absolute;left:99px;top:14px;display:flex;align-items:center;gap:8px}
.brand-dot{width:40px;height:40px;border-radius:50%;background:var(--navy)}
.brand-name{font-weight:700;font-size:30px;color:var(--navy);letter-spacing:0.5px}
.main-nav{position:absolute;right:100px;top:28px;display:flex;gap:42px}
.main-nav a{font-size:14px;letter-spacing:1.4px;color:#333;text-decoration:none;font-weight:500}
.main-nav a.active{color:var(--navy)}

/* hero */
.hero{position:absolute;top:75px;left:0;width:1200px;height:590px;
  background:linear-gradient(100deg,#5d564f 0%,#8c8680 30%,#bfc2c6 55%,#a5a6a8 75%,#3b3631 100%)}
.hero-shade{position:absolute;inset:0;background:rgba(20,20,30,0.25)}
.hero-title{position:absolute;top:190px;width:100%;text-align:center;color:var(--white);font-weight:900;font-size:55px;letter-spacing:1px}
.hero-sub{position:absolute;top:256px;left:250px;width:700px;text-align:center;color:var(--white);font-size:22px;font-weight:400;line-height:28px;letter-spacing:0.8px}
.btn{display:flex;align-items:center;justify-content:center;background:var(--navy);color:var(--white);font-weight:600;font-size:16px;border-radius:26px;text-decoration:none;letter-spacing:0.5px}
.hero .btn{position:absolute;left:517px;top:341px;width:165px;height:49px}
.hero-badge{position:absolute;left:562px;top:620px;width:76px;height:76px;border-radius:50%;background:var(--white);display:flex;align-items:center;justify-content:center}
.hero-badge span{width:52px;height:52px;border-radius:50%;background:var(--navy)}

/* welcome */
.welcome-title{top:756px;width:100%;text-align:center;font-weight:900;font-size:38px}
.welcome-text{top:818px;left:140px;width:920px;text-align:center;font-size:14px;font-weight:300;color:var(--text);line-height:25px}
.welcome-btn{position:absolute;left:517px;top:942px;width:165px;height:49px}

/* mission */
.mission-band{top:1116px;left:0;width:1200px;height:443px;background:var(--band)}
.mission-photo{top:1094px;left:356px;width:488px;height:488px;border-radius:50%;
  background:linear-gradient(180deg,#5a4b40 0%,#6d7d92 45%,#3a5488 75%,var(--navy) 100%)}
.mission-title{top:1317px;width:100%;text-align:center;color:var(--white);font-weight:900;font-size:38px}
.mission-card{position:absolute;width:285px;height:137px;background:var(--white);padding:14px 22px 18px;display:flex;flex-direction:column;justify-content:space-between}
.mission-card p{font-size:17px;font-weight:500;line-height:22px;color:#222;letter-spacing:0.3px}
.mission-card.right{align-items:flex-end;text-align:right}
.mission-card svg{stroke:var(--navy);fill:none;stroke-width:2.4}

/* blog */
.blog-title{top:1670px;width:100%;text-align:center;font-weight:900;font-size:38px}
.post{position:absolute;top:1732px;width:329px}
.post-image{width:329px;height:217px}
.post-date{margin-top:10px;font-size:13px;color:#777;font-weight:300}
.post-title{margin-top:14px;font-size:16.5px;font-weight:500;line-height:20px;color:#111}
.post-excerpt{margin-top:12px;font-size:13px;font-weight:300;color:var(--text);line-height:22.5px}
.post-author{margin-top:18px;display:flex;align-items:center;gap:13px}
.avatar{width:45px;height:45px;border-radius:50%;background:linear-gradient(135deg,#c9b8a6,#7c6a5c)}
.author-name{font-size:14px;font-weight:500;color:#111}
.author-note{font-size:13px;font-weight:300;color:#777;margin-top:3px}

/* footer */
.site-footer{top:2265px;left:0;width:1200px;height:470px;background:var(--navy);color:var(--white)}
.footer-brand{position:absolute;left:98px;top:62px;display:flex;align-items:center;gap:12px}
.footer-brand .brand-dot{width:62px;height:62px;background:var(--white)}
.footer-brand .brand-name{color:var(--white);font-size:44px}
.social{position:absolute;left:96px;top:160px;display:flex;gap:26px}
.social span{width:12px;height:12px;border-radius:50%;background:var(--white)}
.footer-col{position:absolute;top:78px}
.footer-col h4{font-size:20px;font-weight:500;letter-spacing:0.5px;margin-bottom:20px}
.footer-col li{list-style:none;font-size:13.5px;line-height:26.4px}
.footer-col .gap{height:26px}
.footer-rule{position:absolute;left:96px;width:1006px;height:1px;background:rgba(255,255,255,0.12)}
.newsletter-title{position:absolute;left:96px;top:352px;font-size:26px;font-weight:500;letter-spacing:0.4px}
.newsletter-input{position:absolute;left:460px;top:348px;width:475px;height:39px;background:var(--navy-deep);font-size:13.5px;padding:11px 12px}
.newsletter-btn{position:absolute;left:948px;top:348px;width:154px;height:39px;background:var(--white);color:var(--navy);font-size:13px;font-weight:600;display:flex;align-items:center;justify-content:center}
.copyright{position:absolute;top:436px;width:100%;text-align:center;font-size:10px;font-weight:300}
.corner-code{position:absolute;right:36px;top:436px;font-size:10px;font-weight:300}
</style>
</head>
<body>

<header class="site-header">
  <div class="brand"><span class="brand-dot"></span><span class="brand-name">Tallo</span></div>
  <nav class="main-nav">
    <a class="active" href="#">HOME</a><a href="#">ABOUT US</a><a href="#">SERVICES</a><a href="#">OUR MISSION</a><a href="#">BLOG</a><a href="#">CONTACT US</a>
  </nav>
</header>

<section class="hero" role="img" aria-label="Photo of consultants smiling in a business meeting">
  <div class="hero-shade"></div>
  <h1 class="hero-title">TALLO CONSULTING</h1>
  <p class="hero-sub">A Management Consulting company providing consultation in the payment ecosystem</p>
  <a class="btn" href="#">Get Started</a>
</section>
<div class="hero-badge"><span></span></div>

<h2 class="abs welcome-title">Welcome To Tallo Consulting</h2>
<p class="abs welcome-text">Lorem ipsum dolor sit amet, consectetur adipiscing elit, sed do eiusmod tempor incididunt ut labore et dolore magna aliqua. Ut enim ad minim veniam, quis nostrud exercitation ullamco laboris nisi ut aliquip ex ea commodo consequat. Duis aute irure dolor in reprehenderit in voluptate velit esse cillum dolore eu fugiat nulla pariatur. Excepteur sint occaecat cupidatat non proident, sunt in culpa qui officia deserunt mollit anim id est laborum</p>
<a class="btn welcome-btn" href="#">Read More</a>

<section>
  <div class="abs mission-band"></div>
  <div class="abs mission-photo" role="img" aria-label="Photo of a smiling man holding a payment card"></div>
  <h2 class="abs mission-title">OUR MISSION</h2>

  <div class="mission-card" style="left:172px;top:1163px">
    <svg width="56" height="56" viewBox="0 0 56 56"><circle cx="28" cy="12" r="8"/><path d="M14 32c0-8 6-12 14-12s14 4 14 12z"/><path d="M10 40l2 4 4 .5-3 3 .8 4-3.8-2-3.8 2 .8-4-3-3 4-.5z M28 40l2 4 4 .5-3 3 .8 4-3.8-2-3.8 2 .8-4-3-3 4-.5z M46 40l2 4 4 .5-3 3 .8 4-3.8-2-3.8 2 .8-4-3-3 4-.5z"/></svg>
    <p>Assist Our Clients In<br>Reviewing Their Sales</p>
  </div>
  <div class="mission-card right" style="left:742px;top:1163px">
    <svg width="64" height="60" viewBox="0 0 64 60"><circle cx="13" cy="20" r="7"/><circle cx="51" cy="20" r="7"/><path d="M24 6h18l-4-3M42 6l-4 3"/><circle cx="32" cy="40" r="7"/><path d="M22 58c0-6 4-9 10-9s10 3 10 9M8 34v10M14 36v8M50 34v10M56 36v8"/></svg>
    <p>Operation And<br>IT Processes</p>
  </div>
  <div class="mission-card" style="left:172px;top:1375px;padding-left:16px">
    <svg width="64" height="60" viewBox="0 0 64 60"><rect x="16" y="4" width="44" height="34" rx="3"/><path d="M16 12h44"/><rect x="22" y="18" width="10" height="10"/><circle cx="44" cy="23" r="5"/><circle cx="50" cy="23" r="5"/><path d="M2 40h8v18H2zM10 44h14c4 0 6 2 6 4H18M30 48l16-6c4 0 4 4 0 6l-18 8H10"/></svg>
    <p>Purchasing</p>
  </div>
  <div class="mission-card right" style="left:742px;top:1375px;padding-right:18px">
    <svg width="54" height="50" viewBox="0 0 54 50"><rect x="10" y="14" width="22" height="32" rx="3"/><rect x="14" y="18" width="14" height="8"/><path d="M14 32h4M20 32h4M26 32h2M14 38h4M20 38h4M26 38h2M4 46h46M32 30l14-8 4 6-14 8M12 2v8M18 4v6"/></svg>
    <p>To Support Them In Identifying<br>The Best Solution In The Use Of<br>Payment Systems</p>
  </div>
</section>

<h2 class="abs blog-title">Blog</h2>

<article class="post" style="left:98px">
  <div class="post-image" role="img" aria-label="Photo of hands reviewing a printed sales chart" style="background:linear-gradient(135deg,#5b5350,#d9d6d4 55%,#efeeec)"></div>
  <p class="post-date">March 25,2021</p>
  <h3 class="post-title">Lorem ipsum dolor sit amet, consectetur adipiscing elit, sed do eiusmod</h3>
  <p class="post-excerpt">Lorem ipsum dolor sit amet, consectetur adipiscing elit, sed do eiusmod tempor incididunt ut labore et dolore magna aliqua.</p>
  <div class="post-author"><span class="avatar"></span><div><p class="author-name">Mira Lund</p><p class="author-note">Lorem ipsum dolor sit amet</p></div></div>
</article>
<article class="post" style="left:435px">
  <div class="post-image" role="img" aria-label="Photo of a phone paying at a card terminal" style="background:linear-gradient(135deg,#3a2a20,#7a5a40 50%,#2b2522)"></div>
  <p class="post-date">March 25,2021</p>
  <h3 class="post-title">Lorem ipsum dolor sit amet, consectetur adipiscing elit, sed do eiusmod</h3>
  <p class="post-excerpt">Lorem ipsum dolor sit amet, consectetur adipiscing elit, sed do eiusmod tempor incididunt ut labore et dolore magna aliqua.</p>
  <div class="post-author"><span class="avatar"></span><div><p class="author-name">Mira Lund</p><p class="author-note">Lorem ipsum dolor sit amet</p></div></div>
</article>
<article class="post" style="left:774px">
  <div class="post-image" role="img" aria-label="Photo of a team gathered around a meeting table" style="background:linear-gradient(135deg,#6b6660,#b8b4ae 50%,#4a4540)"></div>
  <p class="post-date">March 25,2021</p>
  <h3 class="post-title">Lorem ipsum dolor sit amet, consectetur adipiscing elit, sed do eiusmod</h3>
  <p class="post-excerpt">Lorem ipsum dolor sit amet, consectetur adipiscing elit, sed do eiusmod tempor incididunt ut labore et dolore magna aliqua.</p>
  <div class="post-author"><span class="avatar"></span><div><p class="author-name">Mira Lund</p><p class="author-note">Lorem ipsum dolor sit amet</p></div></div>
</article>

<footer class="abs site-footer">
  <div class="footer-brand"><span class="brand-dot"></span><span class="brand-name">Tallo</span></div>
  <div class="social" aria-label="Social links"><span></span><span></span><span></span><span></span></div>

  <div class="footer-col" style="left:427px">
    <h4>Links</h4>
    <ul><li>Home</li><li>About Us</li><li>Services</li><li>Our Mission</li><li>Blog</li><li>Contact Us</li></ul>
  </div>
  <div class="footer-col" style="left:669px">
    <h4>Others</h4>
    <ul><li>FAQ</li><li>Privacy Policy</li><li>Terms &amp; Conditions</li></ul>
  </div>
  <div class="footer-col" style="left:962px">
    <h4>Contact Us</h4>
    <ul><li>1420 Alder Crest</li><li>Avenue, Brookvale, WI</li><li class="gap"></li><li>+1 555 014 2290</li><li class="gap"></li><li>hello@talloconsult.example</li></ul>
  </div>

  <div class="footer-rule" style="top:322px"></div>
  <h3 class="newsletter-title">Subscribe Our Newsletter</h3>
  <div class="newsletter-input">Email Address</div>
  <div class="newsletter-btn">Subscribe Now</div>
  <div class="footer-rule" style="top:414px"></div>
  <p class="copyright">© Copyrights.2021.The Company Name.All Rights Reserved</p>
  <span class="corner-code">C28</span>
</footer>

</body>
</html>
```